Core Values Banner For Hearthwell Guards Inc

We want to take the core values for our small growing chimney service company and post them for our entire team to see on a daily basis. We want to be remind everyone how important this is too us all. IntegrityWe try to be honest and accountable in all aspects of our business, as well as in our personal interactions. We do what we say we will do, when we say we will do it, and how we say we will do it.Kaizen“Change for the best”We strive to constantly grow and improve, both personally and professionally. We own up to our mistakes and strive to resolve and learn from them. We actively seek feedback from our clients and each other. We believe the most innovative ideas come when we intentionally look for them.FamilyWe are a family-owned business, and we consider everyone who works here and every one we serve to be part of the family. Being honest and genuine with each other and our customers is what sets us apart. We put ourselves in our customer’s shoes and make recommendations as if it were our chimney, our home and our family.

Font styles to use
Serif
Sans Serif

Colors
ec1f27

Requirements
Must have
• This banner will be approximately 2.5' in height and 6 to 6.5' in width.
• I would like all 3 core values and there definitions listed on the banner
• check out the feel of our marketing on our website www.hearthwellguardsnx.com

```html
<!DOCTYPE html>
<html lang="en">
<head>
<meta charset="utf-8">
<title>Hearthwell Guards Inc — Core Values Banner</title>
<link rel="stylesheet" href="https://fonts.googleapis.com/css2?family=Lato:wght@400;700;900&display=swap">
<style>
  :root {
    --page-bg: #f3f3f3;
    --panel-red: #cf1f3c;
    --panel-pink: #d02458;
    --frame-white: #ffffff;
    --ink-white: #ffffff;
    --ghost: rgba(255, 255, 255, 0.08);
  }
  * { box-sizing: border-box; margin: 0; padding: 0; }
  html, body {
    width: 1200px;
    height: 540px;
    overflow: hidden;
    background: var(--page-bg);
  }
  .canvas {
    position: relative;
    width: 1200px;
    height: 540px;
    overflow: hidden;
  }
  .banner {
    position: absolute;
    left: 0;
    top: 39px;
    width: 1352px;
    height: 520px;
    display: flex;
    transform: scale(0.8876);
    transform-origin: top left;
    font-family: "Lato", Arial, sans-serif;
    color: var(--ink-white);
  }
  .value-panel {
    position: relative;
    width: 451px;
    height: 520px;
    background: var(--panel-red);
  }
  .value-panel--kaizen { background: var(--panel-pink); width: 450px; }
  .value-frame {
    position: absolute;
    left: 51px;
    top: 44px;
    width: 369px;
    height: 431px;
    border: 14px solid var(--frame-white);
    overflow: hidden;
  }
  .frame-notch-top,
  .frame-notch-bottom { position: absolute; background: var(--panel-red); }
  .value-panel--kaizen .frame-notch-top,
  .value-panel--kaizen .frame-notch-bottom { background: var(--panel-pink); }
  .frame-notch-top { left: 230px; top: 44px; width: 11px; height: 14px; }
  .frame-notch-bottom { left: 197px; top: 455px; width: 77px; height: 22px; }
  .base-block {
    position: absolute;
    left: 215px;
    top: 448px;
    width: 42px;
    height: 42px;
    background: var(--frame-white);
  }
  .ghost-word {
    position: absolute;
    left: 0;
    width: 100%;
    white-space: nowrap;
    font-weight: 900;
    font-size: 88px;
    line-height: 1;
    color: var(--ghost);
    text-align: center;
  }
  .ghost-word--top { top: 2px; }
  .ghost-word--bottom { bottom: -24px; }
  .value-icon {
    position: absolute;
    left: 196px;
    width: 80px;
    height: 72px;
  }
  .value-title {
    position: absolute;
    left: 0;
    width: 100%;
    text-align: center;
    font-weight: 700;
    font-size: 44px;
    line-height: 1;
    top: 178px;
  }
  .value-motto {
    position: absolute;
    left: 0;
    width: 100%;
    text-align: center;
    font-weight: 700;
    font-size: 24px;
    line-height: 1;
    top: 229px;
  }
  .value-text {
    position: absolute;
    font-size: 12.6px;
    line-height: 19.4px;
    text-align: justify;
    text-align-last: center;
    hyphens: auto;
  }
  .value-panel--integrity .value-text { top: 293px; left: 103px; width: 266px; }
  .value-panel--kaizen .value-text { top: 284px; left: 84px; width: 280px; }
  .value-panel--family .value-text { top: 275px; left: 79px; width: 280px; }
</style>
</head>
<body>
<div class="canvas">
  <section class="banner" aria-label="Hearthwell Guards Inc core values">

    <article class="value-panel value-panel--integrity">
      <div class="value-frame">
        <span class="ghost-word ghost-word--top" aria-hidden="true">Integrity</span>
      </div>
      <div class="frame-notch-top"></div>
      <div class="frame-notch-bottom"></div>
      <div class="base-block" aria-hidden="true"></div>
      <svg class="value-icon" style="top:96px" viewBox="0 0 80 72" aria-hidden="true" fill="#fff" stroke="#fff">
        <circle cx="40" cy="6" r="3" stroke="none"/>
        <rect x="38" y="8" width="4" height="52" stroke="none"/>
        <rect x="14" y="16" width="52" height="3" stroke="none"/>
        <line x1="17" y1="18" x2="8" y2="40" stroke-width="1.5"/>
        <line x1="17" y1="18" x2="26" y2="40" stroke-width="1.5"/>
        <line x1="63" y1="18" x2="54" y2="40" stroke-width="1.5"/>
        <line x1="63" y1="18" x2="72" y2="40" stroke-width="1.5"/>
        <path d="M5 40 H29 A12 9 0 0 1 5 40 Z" stroke="none"/>
        <path d="M51 40 H75 A12 9 0 0 1 51 40 Z" stroke="none"/>
        <path d="M30 62 H50 V66 H30 Z M24 66 H56 V70 H24 Z" stroke="none"/>
      </svg>
      <h2 class="value-title">Integrity</h2>
      <p class="value-text" lang="en">We try to be honest and accountable in all aspects of our business, as well as in our personal interactions. We do what we say we will do, when we say we will do it, and how we say we will do it.</p>
    </article>

    <article class="value-panel value-panel--kaizen">
      <div class="value-frame">
        <span class="ghost-word ghost-word--bottom" aria-hidden="true">Kaizen</span>
      </div>
      <div class="frame-notch-top"></div>
      <div class="frame-notch-bottom"></div>
      <div class="base-block" aria-hidden="true"></div>
      <svg class="value-icon" style="top:96px" viewBox="0 0 80 72" aria-hidden="true" fill="#fff" stroke="#fff">
        <path d="M12 30 A28 28 0 0 1 62 18" fill="none" stroke-width="4"/>
        <path d="M56 12 L68 14 L64 26 Z" stroke="none"/>
        <path d="M68 42 A28 28 0 0 1 18 54" fill="none" stroke-width="4"/>
        <path d="M24 60 L12 58 L16 46 Z" stroke="none"/>
        <rect x="26" y="40" width="5" height="8" stroke="none"/>
        <rect x="33" y="36" width="5" height="12" stroke="none"/>
        <rect x="40" y="32" width="5" height="16" stroke="none"/>
        <rect x="47" y="27" width="5" height="21" stroke="none"/>
        <path d="M26 36 L40 26 L52 18" fill="none" stroke-width="2"/>
        <path d="M48 16 L55 15 L53 22 Z" stroke="none"/>
      </svg>
      <h2 class="value-title">Kaizen</h2>
      <p class="value-motto">“Change for the best”</p>
      <p class="value-text">We strive to constantly grow and improve, both personally and professionally. We own up to our mistakes and strive to resolve and learn from them. We actively seek feedback from our clients and each other. We believe the most innovative ideas come when we intentionally look for them.</p>
    </article>

    <article class="value-panel value-panel--family">
      <div class="value-frame">
        <span class="ghost-word ghost-word--top" aria-hidden="true">Family</span>
      </div>
      <div class="frame-notch-top"></div>
      <div class="frame-notch-bottom"></div>
      <div class="base-block" aria-hidden="true"></div>
      <svg class="value-icon" style="top:100px" viewBox="0 0 80 72" aria-hidden="true" fill="#fff">
        <circle cx="16" cy="14" r="8"/><circle cx="40" cy="14" r="8"/><circle cx="64" cy="14" r="8"/>
        <path d="M3 48 V34 Q3 25 12 25 H20 Q29 25 29 34 V48 Z"/>
        <path d="M27 48 V34 Q27 25 36 25 H44 Q53 25 53 34 V48 Z"/>
        <path d="M51 48 V34 Q51 25 60 25 H68 Q77 25 77 34 V48 Z"/>
      </svg>
      <h2 class="value-title">Family</h2>
      <p class="value-text">We are a family-owned business, and we consider everyone who works here and every one we serve to be part of the family. Being honest and genuine with each other and our customers is what sets us apart. We put ourselves in our customer’s shoes and make recommendations as if it were our chimney, our home and our family.</p>
    </article>

  </section>
</div>
</body>
</html>
```